3D abstract logo Construction, Kitchen and Bath design and Project Management Business Card Design

I want a 3d abstract logo for a new General Construction, Kitchen and Bath design and Project Management Company located at Philadelphia PA, we want to put our logo in the white color trucks too. I want to look professional and serious at the same time look like an architect design and the warm originals color that make you feel in a nice decorated home, I like the colors trend in this link:
http://www.quellmark.example/qm/ggs/pageeditor.aspx?alt_doc_id=RT41K-M9B33-2W5&doc_id=5913046628&pf_id=D4H

I was thinking about a roof and the PA font could have square shape or like wood framing with two tones of the brick color black and creamy yellow color.... Also I like the keystone Idea like the modification or the Ridgeline Parkway logo but curvy at the top

The final design should communicate big company (because we want to grow), responsible, professional and organized that really care about our customers and give them everything they need... plan and design, excellent labor and Project Management
Updates

I doesn't have to be 3d

Reason: I haven't received enough options...

Please stick with the warm tones shown in the image001 attached I like spicy cinnamon instead a cold wine or brick color and also the cream yellowish tones added

Hello designers, please use only the idea and colors of the image001 I don't want to be stick with a house logo because I do commercial construction too so I prefer work around the keystone idea maybe leaving the style of the PA.
I'd like the base tone on the card dark like first option and you can send me a white option too.

Please send me your ideas as soon as possible 

Thank you so much!

Target Market(s)

Builders, State, commercial business owners, Property owners or Real State and Property Management Companies

Industry/Entity Type

Architect

Contact Information for Business Card

RK Buildworks LLC
“Your project is our business”
Lorna Vasquel Eng.
President
Commercial & Residential General Construction
Kitchen & Bath Design | Project Management
Phone: 555-304-7718 | Fax: 555-304-7719 Cell: 555-862-3097
lorna@rkbuildworks.example

```html
<!DOCTYPE html>
<html lang="en">
<head>
<meta charset="utf-8">
<title>RK Buildworks – Business Cards</title>
<link rel="stylesheet" href="https://fonts.googleapis.com/css2?family=Arimo:ital,wght@0,400;0,700;1,400&family=Ubuntu:wght@400&display=swap">
<style>
  :root {
    --cream: #fdfae6;
    --cinnamon: #a8001a;
    --cinnamon-text: #b0101e;
    --rose: #d5304a;
    --soft-red: #e2241c;
    --amber: #e9b431;
    --ink: #1a1a1a;
    --page: #ffffff;
  }
  * { margin: 0; padding: 0; box-sizing: border-box; }
  html, body { width: 1200px; height: 947px; overflow: hidden; background: var(--page); }
  .sheet { position: relative; width: 1200px; height: 947px; }

  .card-front { position: absolute; display: block; }
  .card-front--dark-circle { left: 0; top: 3px; }
  .card-front--amber-circle { left: 617px; top: 0; }

  .card-front .bg { fill: var(--cream); }
  .card-front .band { fill: var(--cinnamon); }
  .card-front .arc-amber { fill: none; stroke: var(--amber); stroke-width: 4; }
  .card-front .arc-rose { fill: none; stroke: var(--rose); stroke-width: 5; }
  .card-front .arc-red { fill: none; stroke: var(--soft-red); stroke-width: 4; }
  .card-front .seal { fill: var(--cream); }
  .card-front .seal-inner { fill: var(--amber); }

  .name { font-family: "Arimo", sans-serif; font-weight: 700; font-size: 30px; fill: var(--cinnamon); }
  .role { font-family: "Arimo", sans-serif; font-style: italic; font-size: 20px; fill: var(--cinnamon); }
  .services { font-family: "Ubuntu", sans-serif; font-size: 18.5px; fill: var(--rose); }
  .label { font-family: "Arimo", sans-serif; font-size: 14.5px; fill: var(--cinnamon-text); }
  .value { font-family: "Arimo", sans-serif; font-size: 14.5px; fill: var(--ink); }
  .brand-small { font-family: "Ubuntu", sans-serif; font-size: 15px; fill: var(--cinnamon); }
  .brand-small--light { fill: var(--cream); }

  .card-back {
    position: absolute;
    width: 342px;
    height: 582px;
    background: var(--cream);
    display: flex;
    flex-direction: column;
    align-items: center;
    font-family: "Arimo", sans-serif;
    color: var(--cinnamon-text);
  }
  .card-back--square { left: 107px; top: 364px; }
  .card-back--circle { left: 725px; top: 360px; }

  .brand-block {
    margin-top: 175px;
    height: 175px;
    display: flex;
    align-items: center;
    justify-content: center;
    gap: 14px;
  }
  .brand-square { width: 46px; height: 46px; background: var(--cinnamon); }
  .brand-circle-wrap { position: relative; width: 210px; height: 170px; display: flex; align-items: center; justify-content: center; }
  .brand-circle { position: absolute; right: 0; top: 0; width: 170px; height: 170px; border-radius: 50%; background: var(--amber); }
  .brand-name {
    position: relative;
    font-family: "Ubuntu", sans-serif;
    font-size: 30px;
    font-weight: 400;
    color: var(--cinnamon);
    line-height: 1.05;
    text-align: left;
  }
  .card-back--circle .brand-name { color: var(--cream); text-align: center; margin-left: 40px; }
  .tagline { margin-top: 22px; font-size: 18px; }
  .web { margin-top: auto; margin-bottom: 66px; font-size: 14.5px; color: var(--rose); }
</style>
</head>
<body>
<main class="sheet">

  <svg class="card-front card-front--dark-circle" width="584" height="342" viewBox="0 0 555 325" aria-label="Business card front, cinnamon band">
    <rect class="bg" x="0" y="0" width="555" height="325"/>
    <path class="band" d="M478,0 L555,0 L555,325 L330,325 C420,305 500,230 505,150 C508,90 495,40 478,0 Z"/>
    <path class="arc-rose" d="M462,0 C490,60 500,130 488,185"/>
    <path class="arc-red" d="M470,0 C498,60 506,130 494,185"/>
    <path class="arc-amber" d="M487,0 C510,60 512,120 500,175"/>
    <path class="arc-amber" d="M330,323 C360,310 390,295 410,280"/>
    <path class="arc-rose" d="M345,325 C375,312 400,298 420,285"/>
    <path class="arc-red" d="M390,325 C405,315 418,305 428,295"/>
    <circle class="seal" cx="462" cy="252" r="60"/>
    <text class="brand-small" x="462" y="248" text-anchor="middle">RK</text>
    <text class="brand-small" x="462" y="266" text-anchor="middle">Buildworks</text>

    <text class="name" x="28" y="54">LORNA VASQUEL</text>
    <text class="role" x="28" y="83">Eng. President</text>
    <text class="services" x="28" y="125">Commercial &amp; Residential General</text>
    <text class="services" x="28" y="147">Construction Kitchen &amp; Bath Design</text>
    <text class="label" x="28" y="231">Phone:</text><text class="value" x="104" y="231">555-304-7718</text>
    <text class="label" x="28" y="255">Fax:</text><text class="value" x="104" y="255">555-304-7719</text>
    <text class="label" x="28" y="279">Cell:</text><text class="value" x="104" y="279">555-862-3097</text>
    <text class="label" x="28" y="303">Email:</text><text class="value" x="104" y="303">lorna@rkbuildworks.example</text>
  </svg>

  <svg class="card-front card-front--amber-circle" width="583" height="343" viewBox="0 0 555 325" aria-label="Business card front, amber seal">
    <rect class="bg" x="0" y="0" width="555" height="325"/>
    <path class="band" d="M478,0 L555,0 L555,325 L330,325 C420,305 500,230 505,150 C508,90 495,40 478,0 Z"/>
    <path class="arc-rose" d="M462,0 C490,60 500,130 488,185"/>
    <path class="arc-red" d="M470,0 C498,60 506,130 494,185"/>
    <path class="arc-amber" d="M487,0 C510,60 512,120 500,175"/>
    <path class="arc-amber" d="M330,323 C360,310 390,295 410,280"/>
    <path class="arc-rose" d="M345,325 C375,312 400,298 420,285"/>
    <path class="arc-red" d="M390,325 C405,315 418,305 428,295"/>
    <circle class="seal" cx="458" cy="243" r="60"/>
    <circle class="seal-inner" cx="458" cy="243" r="47"/>
    <text class="brand-small brand-small--light" x="458" y="240" text-anchor="middle">RK</text>
    <text class="brand-small brand-small--light" x="458" y="258" text-anchor="middle">Buildworks</text>

    <text class="name" x="28" y="52">LORNA VASQUEL</text>
    <text class="role" x="28" y="81">Eng. President</text>
    <text class="services" x="28" y="123">Commercial &amp; Residential General</text>
    <text class="services" x="28" y="145">Construction Kitchen &amp; Bath Design</text>
    <text class="label" x="28" y="229">Phone:</text><text class="value" x="104" y="229">555-304-7718</text>
    <text class="label" x="28" y="253">Fax:</text><text class="value" x="104" y="253">555-304-7719</text>
    <text class="label" x="28" y="277">Cell:</text><text class="value" x="104" y="277">555-862-3097</text>
    <text class="label" x="28" y="301">Email:</text><text class="value" x="104" y="301">lorna@rkbuildworks.example</text>
  </svg>

  <section class="card-back card-back--square">
    <div class="brand-block">
      <span class="brand-square"></span>
      <span class="brand-name">RK<br>Buildworks</span>
    </div>
    <p class="tagline">Your project is our business</p>
    <p class="web">www.rkbuildworks.example</p>
  </section>

  <section class="card-back card-back--circle">
    <div class="brand-block">
      <div class="brand-circle-wrap">
        <span class="brand-circle"></span>
        <span class="brand-name">RK<br>Buildworks</span>
      </div>
    </div>
    <p class="tagline">Your project is our business</p>
    <p class="web">www.rkbuildworks.example</p>
  </section>

</main>
</body>
</html>
```